BrindleStaffing Business Card Design

We are a staffing company finding positions for dedicated nurses and physicians.

Target Market(s)

Business Professionals

Industry/Entity Type

Staffing

Contact Information for Business Card

Gordon Pratley
Chairman
417 39th Avenue South
SAINT PETERSBURG FL 33712
813-555-4172 Mobile
813-555-8036 Fax
gpratley@brindlestaffing.com
www.brindlestaffing.com

Font styles to use
Sans Serif

Colors
fbee3e
f04a50
f37122

Requirements
Must have
• Logo Attached, see colors below. We'd like to see Yellow, Orange and Red.

```html
<!DOCTYPE html>
<html lang="en">
<head>
<meta charset="utf-8">
<title>BrindleStaffing Business Card</title>
<link href="https://fonts.googleapis.com/css2?family=Source+Sans+3:wght@400;600;700&display=swap" rel="stylesheet">
<style>
  :root {
    --stage: #eceae7;
    --brand-red: #f04a50;
    --brand-orange: #f37122;
    --brand-yellow: #fbee3e;
    --card-white: #ffffff;
    --ink-white: #ffffff;
    --ink-dark: #3a3a3a;
  }
  * { margin: 0; padding: 0; box-sizing: border-box; }
  html, body {
    width: 1200px; height: 768px; overflow: hidden;
    background: var(--stage);
    font-family: "Source Sans 3", Arial, sans-serif;
  }
  .stage {
    width: 1200px; height: 768px;
    display: flex; align-items: center; justify-content: center; gap: 40px;
  }
  .card {
    position: relative;
    width: 540px; height: 309px;
    border-radius: 16px; overflow: hidden;
    box-shadow: 0 6px 18px rgba(0,0,0,0.15);
  }
  .card-front { background: var(--card-white); }
  .card-back { background: var(--brand-red); display: flex; align-items: center; justify-content: center; }
  .bands { position: absolute; inset: 0; }
  .band-top { fill: var(--brand-red); }
  .band-bottom { fill: var(--brand-orange); }
  .band-accent { fill: var(--brand-yellow); }

  .identity {
    position: absolute; left: 26px; top: 22px;
    color: var(--ink-white);
  }
  .identity-name { font-size: 21px; font-weight: 700; line-height: 1.1; }
  .identity-title { font-size: 14px; font-weight: 400; margin-bottom: 4px; }
  .identity-address { font-size: 13px; line-height: 1.3; }

  .wordmark {
    font-weight: 600;
    white-space: nowrap;
  }
  .card-front .wordmark {
    position: absolute; left: 0; right: 0; top: 130px;
    text-align: center;
    font-size: 38px; color: var(--brand-orange);
  }
  .card-back .wordmark { font-size: 44px; color: var(--ink-white); }

  .contact {
    position: absolute; right: 16px; bottom: 16px;
    list-style: none; color: var(--ink-white);
    font-size: 13px; line-height: 19px; text-align: right;
  }
  .contact li { display: flex; align-items: center; justify-content: flex-end; gap: 7px; }
  .contact svg { width: 11px; height: 11px; flex: none; }
</style>
</head>
<body>
<main class="stage">
  <section class="card card-front" aria-label="Business card front">
    <svg class="bands" viewBox="0 0 540 309" preserveAspectRatio="none">
      <path class="band-top" d="M0 0 H540 V22 H320 C285 22 280 45 270 70 C258 100 245 112 210 112 H0 Z"/>
      <path class="band-accent" d="M0 309 H540 V169 H396 C361 169 356 189 346 214 C334 246 326 284 286 284 H0 Z"/>
      <path class="band-bottom" d="M0 309 H540 V175 H400 C365 175 360 195 350 220 C338 252 330 290 290 290 H0 Z"/>
    </svg>

    <div class="identity">
      <p class="identity-name">Gordon Pratley</p>
      <p class="identity-title">Chairman</p>
      <p class="identity-address">417 39th Avenue South<br>Saint Petersburg FL 33712</p>
    </div>

    <p class="wordmark">BrindleStaffing</p>

    <ul class="contact">
      <li>813-555-4172
        <svg viewBox="0 0 12 12"><rect x="3" y="0.7" width="6" height="10.6" rx="1.2" fill="none" stroke="#fff" stroke-width="1.3"/><circle cx="6" cy="9.2" r="0.7" fill="#fff"/></svg></li>
      <li>813-555-8036
        <svg viewBox="0 0 12 12"><rect x="1" y="4" width="10" height="7" rx="1" fill="#fff"/><rect x="3" y="1" width="6" height="3" fill="#fff"/></svg></li>
      <li>gpratley@brindlestaffing.com
        <svg viewBox="0 0 12 12"><rect x="0.7" y="2" width="10.6" height="8" fill="none" stroke="#fff" stroke-width="1.2"/><path d="M1 2.5 L6 7 L11 2.5" fill="none" stroke="#fff" stroke-width="1.2"/></svg></li>
      <li>www.brindlestaffing.com
        <svg viewBox="0 0 12 12"><circle cx="6" cy="6" r="5.3" fill="none" stroke="#fff" stroke-width="1.2"/><ellipse cx="6" cy="6" rx="2.3" ry="5.3" fill="none" stroke="#fff" stroke-width="1"/><path d="M0.8 6 H11.2" stroke="#fff" stroke-width="1"/></svg></li>
    </ul>
  </section>

  <section class="card card-back" aria-label="Business card back">
    <p class="wordmark">BrindleStaffing</p>
  </section>
</main>
</body>
</html>
```